Launching a new real estate agency in Monaco

Hello, I am opening a new real estate agency in Monaco. For the purpose of my activity, in order to be known quickly among a fierce competition I need an advertising campaign that will be broadcast in local magazines, newspapers, paper board, etc.

You will find example of pictures of Monaco on which I have the rights and my logo. You can always pick other images that I can buy if the price is reasonable for a commercial use (<200 $)

Please respect the color code.

I wish you good luck and look forward to give you my feedbacks

Reason: Only few projects posted were respecting the brief and of quality. Hoping to receive more in coming days

Target Market(s)

International high-end clientele of all ages, all genders.

Industry/Entity Type

Real Estate Agent

Font styles to use
Serif

Requirements
Must have
• 1/ My logo
• 2/ This message "Un nouveau regard sur l'immobilier" means in English a fresh look at real estate or new eyes on real-estate.
• 3/ My address: 14 rue des Ormeaux, Galerie Bellerive Nord, 98 000 Monaco
• 4/ Phone number: +377.93.48.25.07
• 5/ Website: www.corvano-immo.com.
• 6/ Format: Files should be easily adjustable but I'd like a vertical display to fit easily in Magazines, Poster and billboard. So please work in high resolution !
Nice to have
• Please think about your design in accordance with the message I want to display.
Should not have
• A simple poster with a picture of Monaco that does not take into consideration the message of the advertisement, "Un nouveau regard sur l'immobilier" which means in english, new eyes on real-estate or a new look at real-estate, or new vision at real-estate.

```html
<!DOCTYPE html>
<html lang="fr">
<head>
<meta charset="utf-8">
<title>Corvano Immo — Un nouveau regard sur l'immobilier</title>
<link rel="stylesheet" href="https://fonts.googleapis.com/css2?family=Forum&family=Quicksand:wght@500&display=swap">
<style>
  :root {
    --paper: #ffffff;
    --purple-deep: #2a0636;
    --purple-mid: #6a0f6e;
    --magenta: #c4329e;
    --rose-gold: #e0a48a;
    --gold-light: #f7dc7a;
    --gold: #d4a52c;
    --gold-dark: #8a6210;
    --text-light: #ffffff;
    --rule: rgba(255,255,255,0.55);
  }
  * { margin: 0; padding: 0; box-sizing: border-box; }
  html, body { width: 889px; height: 1200px; overflow: hidden; background: var(--paper); }
  .poster {
    position: absolute; left: 26px; top: 26px; width: 837px; height: 1148px;
    background: radial-gradient(ellipse 60% 45% at 50% 40%, var(--magenta) 0%, var(--purple-mid) 55%, var(--purple-deep) 100%);
    overflow: hidden;
  }
  .brand {
    position: absolute; top: 118px; left: 0; width: 100%;
    display: flex; justify-content: center; align-items: center; gap: 18px;
  }
  .brand-mark { width: 22px; height: 22px; background: var(--rose-gold); }
  .brand-name {
    font-family: "Forum", serif; font-size: 52px; letter-spacing: 6px;
    color: var(--rose-gold); line-height: 1;
  }
  .headline {
    position: absolute; top: 268px; left: 0; width: 100%; text-align: center;
    font-family: "Forum", serif; font-weight: 400; font-size: 86px; line-height: 78px;
    color: transparent; -webkit-text-stroke: 1.6px var(--text-light);
    letter-spacing: 1px;
  }
  .frame {
    position: absolute; left: 147px; top: 520px; width: 544px; height: 418px;
    background: linear-gradient(135deg, var(--gold-light), var(--gold) 35%, var(--gold-dark) 60%, var(--gold-light) 80%, var(--gold));
    box-shadow: 0 10px 30px rgba(0,0,0,0.45);
  }
  .frame::before {
    content: ""; position: absolute; inset: 22px;
    border: 3px solid var(--gold-dark);
  }
  .view {
    position: absolute; left: 55px; top: 55px; width: 434px; height: 308px;
    background: linear-gradient(180deg, #f0a058 0%, #c27aa0 22%, #7a6aa6 45%, #3a2f55 70%, #2a1a2c 100%);
    box-shadow: inset 0 0 0 2px var(--gold-dark);
  }
  .social {
    position: absolute; top: 984px; left: 0; width: 100%;
    display: flex; justify-content: center; gap: 6px;
  }
  .social span {
    width: 34px; height: 34px; border-radius: 50%; background: #2f7dd4;
    border: 2px solid var(--text-light);
  }
  .contact {
    position: absolute; top: 1050px; left: 0; width: 100%;
    display: flex; justify-content: center; gap: 26px;
    font-family: "Quicksand", sans-serif; font-weight: 500; font-size: 25px; color: var(--text-light);
  }
  .contact-item { display: flex; align-items: center; gap: 6px; }
  .contact svg { width: 26px; height: 26px; }
  .rule {
    position: absolute; top: 1088px; left: 42px; width: 753px; height: 1px; background: var(--rule);
  }
  .address {
    position: absolute; top: 1096px; left: 0; width: 100%;
    display: flex; justify-content: center; align-items: center; gap: 4px;
    font-family: "Quicksand", sans-serif; font-weight: 500; font-size: 19px; color: var(--text-light);
  }
  .address svg { width: 20px; height: 20px; }
</style>
</head>
<body>
  <main class="poster">
    <header class="brand">
      <span class="brand-mark"></span>
      <span class="brand-name">CORVANO IMMO</span>
    </header>

    <h1 class="headline">UN NOUVEAU<br>REGARD SUR<br>L'IMMOBILIER</h1>

    <div class="frame">
      <div class="view" role="img" aria-label="Vue de Monaco au coucher du soleil, côte et immeubles illuminés"></div>
    </div>

    <nav class="social" aria-label="Réseaux sociaux">
      <span></span><span></span><span></span>
    </nav>

    <div class="contact">
      <div class="contact-item">
        <svg viewBox="0 0 24 24" fill="none" stroke="currentColor" stroke-width="1.5" stroke-linejoin="round"><path d="M5 3h4l2 5-2.5 1.5a11 11 0 0 0 6 6L16 13l5 2v4a2 2 0 0 1-2 2A17 17 0 0 1 3 5a2 2 0 0 1 2-2z"/></svg>
        <span>+377.93.48.25.07</span>
      </div>
      <div class="contact-item">
        <svg viewBox="0 0 24 24" fill="none" stroke="currentColor" stroke-width="1.5"><circle cx="12" cy="12" r="9"/><ellipse cx="12" cy="12" rx="4" ry="9"/><path d="M3 12h18M5 7h14M5 17h14"/></svg>
        <span>www.corvano-immo.com.</span>
      </div>
    </div>

    <div class="rule"></div>

    <address class="address" style="font-style:normal">
      <svg viewBox="0 0 24 24" fill="none" stroke="currentColor" stroke-width="1.5"><path d="M12 21s-6-6.5-6-11a6 6 0 0 1 12 0c0 4.5-6 11-6 11z"/><circle cx="12" cy="10" r="2.2"/></svg>
      <span>14 rue des Ormeaux, Galerie Bellerive Nord, 98 000 Monaco</span>
    </address>
  </main>
</body>
</html>
```